KRT Engineering Business Card Design

We’re looking for an elegant, clean, and timeless business card design that communicates experience, capability, and reliability.

KRT Engineering was established in 1995 , we are a Government Contracting company providing Professional Services to the Office of Frontier Affairs, Harbor Protection and the Vantage Collective. Our capabilities include: Acquisition & Program Management; Intelligence & Security Operations; Cyber, IT & Network Operations; Lifecycle Logistics & Asset Readiness; C5ISR Systems Engineering & Sustainment.

We want the card to reflect a straightforward, confident approach to business. The design should feel polished and professional without being flashy or overly corporate.

Design Direction
Clean, sophisticated, and uncluttered
Elegant but understated
Strong typography and thoughtful spacing
A timeless aesthetic rather than something overly trendy
Confident and established, with a sense of substance
Easy to read and practical in a real-world business setting

The overall impression should be: “These are experienced professionals who know what they’re doing, do what they say, and can be relied upon.”

We’re open to creative interpretations. The finished card should feel distinctive through its typography, proportions, layout, and attention to detail rather than through excessive graphics or visual effects.

We’re looking for a design that would make a potential client immediately feel that they’re dealing with a capable, trustworthy, and established company.

Company Colors: Navy and Gold/Yellow (but you do not need to use these colors on the card)
Company Name: KRT Engineering Associates, Inc. (known as KRT Engineering)
Website: krtengineering.com
Company Logo: Navy & Gold (other variations attached)

```html
<!DOCTYPE html>
<html lang="en">
<head>
<meta charset="utf-8">
<title>KRT Engineering — Business Card</title>
<link rel="stylesheet" href="https://fonts.googleapis.com/css2?family=Arimo:wght@400;700&display=swap">
<style>
  :root {
    --navy: #1f2a5e;
    --gold: #f2d64b;
    --paper: #f3f3f3;
    --ink: #2a2a2a;
    --backdrop: #1c1c1c;
  }
  * { margin: 0; padding: 0; box-sizing: border-box; }
  html, body {
    width: 1200px;
    height: 1059px;
    overflow: hidden;
    background: var(--backdrop);
    font-family: "Arimo", Arial, sans-serif;
  }
  .card {
    position: absolute;
    width: 690px;
    height: 392px;
    border-radius: 20px;
  }
  .card-front { left: 256px; top: 89px; background: var(--paper); }
  .card-back  { left: 255px; top: 547px; background: var(--navy); }

  .brand {
    position: absolute;
    display: flex;
    align-items: center;
    font-weight: 700;
    letter-spacing: 1px;
  }
  .card-front .brand {
    left: 80px;
    top: 160px;
    width: 250px;
    justify-content: center;
    gap: 12px;
    font-size: 58px;
    color: var(--navy);
  }
  .brand-dot {
    width: 18px;
    height: 18px;
    border-radius: 50%;
    background: var(--gold);
  }
  .card-back .brand {
    left: 0;
    right: 0;
    top: 135px;
    justify-content: center;
    font-size: 110px;
    color: var(--paper);
  }

  .divider {
    position: absolute;
    left: 343px;
    top: 123px;
    width: 1.5px;
    height: 147px;
    background: var(--navy);
  }
  .details {
    position: absolute;
    left: 373px;
    top: 117px;
  }
  .person-name {
    font-size: 23px;
    font-weight: 700;
    color: var(--navy);
    line-height: 1.15;
  }
  .person-title {
    font-size: 18px;
    color: var(--ink);
    line-height: 1.2;
    margin-bottom: 20px;
  }
  .contact-list { list-style: none; }
  .contact-list li {
    display: flex;
    align-items: center;
    gap: 8px;
    font-size: 17.5px;
    color: var(--ink);
    height: 31px;
  }
  .contact-list svg { width: 14px; height: 14px; fill: var(--navy); flex: none; }
</style>
</head>
<body>
  <section class="card card-front">
    <div class="brand"><span class="brand-name">KRT</span><span class="brand-dot"></span></div>
    <div class="divider"></div>
    <div class="details">
      <p class="person-name">Helen R. Marsh</p>
      <p class="person-title">Principal Engineer</p>
      <ul class="contact-list">
        <li>
          <svg viewBox="0 0 24 24" aria-hidden="true"><path d="M6.6 10.8a15.1 15.1 0 0 0 6.6 6.6l2.2-2.2a1 1 0 0 1 1-.25 11.4 11.4 0 0 0 3.6.57 1 1 0 0 1 1 1V20a1 1 0 0 1-1 1A17 17 0 0 1 3 4a1 1 0 0 1 1-1h3.5a1 1 0 0 1 1 1c0 1.25.2 2.45.57 3.57a1 1 0 0 1-.25 1z"/></svg>
          (555) 384-2190
        </li>
        <li>
          <svg viewBox="0 0 24 24" aria-hidden="true"><path d="M2 9l10-7 10 7v12H2zM4.5 10.2 12 15.5l7.5-5.3L12 4.8z"/></svg>
          h.m@krtengineering.com
        </li>
        <li>
          <svg viewBox="0 0 24 24" aria-hidden="true"><path d="M12 2a10 10 0 1 0 0 20 10 10 0 0 0 0-20zm-1 17.9A8 8 0 0 1 4.2 10.4L9 15v1a2 2 0 0 0 2 2zm6.9-2.5A2 2 0 0 0 16 16h-1v-3a1 1 0 0 0-1-1H8v-2h2a1 1 0 0 0 1-1V7h2a2 2 0 0 0 2-2v-.4a8 8 0 0 1 2.9 12.8z"/></svg>
          krtengineering.com
        </li>
      </ul>
    </div>
  </section>

  <section class="card card-back">
    <div class="brand"><span class="brand-name">KRT</span></div>
  </section>
</body>
</html>
```